Dental Medical History Form - Content provided

Design a medical history form for a dental practice. Content is provided so all that is needed is the formatting to make it look great and easy to read.

"Patient Information" to include all information contained in top portion of the "Patient Medical History Form" docx file.

"Medical History" should follow the formatting and content of the "Exact Medical History" file as this is what the entry fields look like in our practice software and so we would like it to match.

1st page - Patient info, allergies, medications, antibiotics, joint replacement, pregnancy.

2nd page - Do you have, or have you had, any of the following? . . . . . . .
Updates

Target Market(s)

All ages but must be clear enough for elderly to read. Use as much space as possible to keep font size bigger yet keep to two pages

Industry/Entity Type

Dental

Font styles to use
Sans Serif

Requirements
Must have
• All content provided
• Our logo at the top (file provided)
• Century Gothic Font
• Limit to two pages

```html
<!DOCTYPE html>
<html lang="en">
<head>
<meta charset="utf-8">
<title>Harbourline Dental – Confidential Medical History</title>
<link href="https://fonts.googleapis.com/css2?family=PT+Sans+Narrow:wght@400;700&family=Questrial&display=swap" rel="stylesheet">
<style>
  :root{
    --backdrop:#e6f3f9;
    --paper:#ffffff;
    --paper-tint:#f1f6fc;
    --navy:#163f8c;
    --blue:#2460b4;
    --sky:#5fb6e0;
    --ink:#1c3f82;
    --rule:#b9d3ec;
    --box:#8fb3dc;
  }
  *{box-sizing:border-box;margin:0;padding:0}
  html,body{width:1200px;height:784px;overflow:hidden}
  body{background:var(--backdrop);font-family:"PT Sans Narrow",sans-serif;color:var(--ink)}
  .form-page{
    position:absolute;left:330px;top:10px;width:540px;height:764px;
    background:linear-gradient(180deg,var(--paper) 0%,var(--paper-tint) 100%);
    box-shadow:0 2px 10px rgba(22,63,140,.15);
    padding:0 18px 0 26px;overflow:hidden;
  }
  .edge-bar{position:absolute;left:0;top:250px;bottom:0;width:8px;background:linear-gradient(90deg,var(--navy),var(--blue))}

  .masthead{display:flex;justify-content:space-between;align-items:flex-start;padding-top:18px;height:64px}
  .brand-name{font-family:"Questrial",sans-serif;font-size:30px;color:var(--ink);line-height:1}
  .brand-name small{display:block;font-size:13px;text-align:right;margin-top:-2px}
  .practice-contact{text-align:right;font-size:9px;font-weight:700;line-height:1.3}
  .practice-phone{display:flex;align-items:center;justify-content:flex-end;gap:5px;font-size:12px}
  .practice-phone svg{width:14px;height:14px}

  .title-band{
    height:15px;margin:0 -18px 8px 60px;
    background:linear-gradient(90deg,var(--sky),var(--blue) 20%,var(--navy));
    clip-path:polygon(12px 0,100% 0,100% 100%,0 100%);
    color:#fff;font-size:8.5px;font-weight:700;letter-spacing:3px;text-align:center;line-height:15px;
  }

  .field-row{display:flex;align-items:flex-end;gap:6px;height:19px;font-size:9.5px}
  .field-row label,.field-row .lbl{white-space:nowrap}
  .entry{flex:1;height:13px;border:1px solid var(--rule);border-radius:1px}
  .entry.short{flex:0 0 70px}
  .tick{display:inline-block;width:9px;height:9px;border:1px solid var(--box);vertical-align:-1px;margin:0 6px 0 3px}

  .section-band{
    height:15px;margin:10px -18px 6px -26px;padding-left:26px;
    background:linear-gradient(90deg,var(--navy) 0%,var(--blue) 65%,var(--sky) 100%);
    color:#fff;font-size:9.5px;font-weight:700;line-height:15px;text-align:center;
  }
  .section-band.lead{background:linear-gradient(90deg,var(--sky),var(--blue) 35%,var(--navy))}

  .check-row{display:flex;justify-content:space-between;height:18px;align-items:center;font-size:9.5px}
  .check-row span{white-space:nowrap}

  .med-lines .line{height:17px;border-bottom:1px solid var(--ink);opacity:.7}

  .question{display:flex;gap:6px;height:18px;align-items:center;font-size:9.5px}
  .question .q{width:160px}
  .question .answers{white-space:nowrap}

  .turnover-tab{
    position:absolute;left:0;bottom:22px;width:120px;height:20px;
    background:linear-gradient(90deg,var(--navy),var(--sky));
    color:#fff;font-size:10px;font-weight:700;line-height:20px;padding-left:18px;
    border-radius:0 6px 6px 0;
  }
</style>
</head>
<body>
<main class="form-page">
  <div class="edge-bar"></div>

  <header class="masthead">
    <div class="brand-name">Harbourline<small>dental</small></div>
    <div class="practice-contact">
      <div class="practice-phone">
        <svg viewBox="0 0 14 14" aria-hidden="true"><rect width="14" height="14" rx="3" fill="#2f8fcf"/><path d="M4.5 3.2l1.3 1.9-.8.9c.5 1.1 1.3 1.9 2.4 2.4l.9-.8 1.9 1.3-.7 1.5c-3 .1-6.1-3-6-6z" fill="#fff"/></svg>
        (02) 4000 1234
      </div>
      Harbourline Dental, Suite 4, 18 Example Rd<br>Westby NSW 2999
    </div>
  </header>

  <div class="title-band">CONFIDENTIAL MEDICAL HISTORY</div>

  <section class="patient-info">
    <div class="field-row"><label>Name:</label><span class="lbl">First</span><span class="entry"></span><span class="lbl">Middle</span><span class="entry"></span><span class="lbl">Last</span><span class="entry"></span></div>
    <div class="field-row"><label>Address:</label><span class="entry"></span></div>
    <div class="field-row"><label>DOB:</label><span class="entry short"></span><label>Email Address:</label><span class="entry"></span></div>
    <div class="field-row"><label>Phone Number(s): Mobile</label><span class="entry"></span><span class="lbl">Work</span><span class="entry"></span><span class="lbl">Home</span><span class="entry"></span></div>
    <div class="field-row"><label>Emergency Contact Person: Name:</label><span class="entry"></span><span class="lbl">Relationship:</span><span class="entry"></span></div>
    <div class="field-row"><span class="entry"></span><span class="lbl">Phone number:</span><span class="entry"></span></div>
  </section>

  <div class="section-band lead">General Practitioner:</div>
  <section class="gp-info">
    <div class="field-row"><label>Name:</label><span class="entry"></span><span class="lbl">Phone Number:</span><span class="entry"></span></div>
    <div class="field-row"><label>Practice Name:</label><span class="entry"></span></div>
    <div class="field-row"><label>Do you have a health fund with dental cover? Yes<span class="tick"></span>or No<span class="tick"></span> If so, what is the name of the fund?</label><span class="entry"></span></div>
    <div class="field-row"><label>Fund Number:</label><span class="entry"></span><span class="lbl">Priority Number on card: 0<span class="tick"></span>1<span class="tick"></span>2<span class="tick"></span>3<span class="tick"></span>4<span class="tick"></span>5<span class="tick"></span></span></div>
    <div class="field-row"><label>Occupation:</label><span class="entry"></span><span class="lbl">Referred by:</span><span class="entry"></span></div>
  </section>

  <div class="section-band">Please indicate if you are allergic to any of the following:</div>
  <section class="allergies">
    <div class="check-row"><span>Aspirin<i class="tick"></i></span><span>Codeine<i class="tick"></i></span><span>Penicillin<i class="tick"></i></span><span>Sulfites<i class="tick"></i></span><span>Latex<i class="tick"></i></span><span>Local Anaesthetic<i class="tick"></i></span><span>Lactose<i class="tick"></i></span><span>Nickel<i class="tick"></i></span></div>
    <div class="field-row"><label>Other:</label><span class="entry"></span></div>
  </section>

  <div class="section-band lead">Are you currently taking, or have ever taken, any of the following medication(s)?</div>
  <section class="medications">
    <div class="check-row"><span>Asthma Inhaler<i class="tick"></i></span><span>Anti-epileptics<i class="tick"></i></span><span>Anti-depressants<i class="tick"></i></span><span>Blood Pressure<i class="tick"></i></span><span>Blood Thinners<i class="tick"></i></span><span>Bisphosphonates<i class="tick"></i></span></div>
    <div class="check-row"><span>Chemotherapy<i class="tick"></i></span><span>Insulin<i class="tick"></i></span><span>Immunosuppressants<i class="tick"></i></span><span>Steroids<i class="tick"></i></span><span>Oral Contraceptive<i class="tick"></i></span><span>Other<i class="tick"></i></span></div>
  </section>

  <div class="section-band">Please specify medication name, dose and frequency where possible:</div>
  <section class="med-lines">
    <div class="line"></div><div class="line"></div><div class="line"></div><div class="line"></div><div class="line"></div>
  </section>

  <section class="health-questions" style="margin-top:12px">
    <div class="question"><span class="q">Do you require antibiotic cover?</span><span class="answers">Yes<i class="tick"></i>No<i class="tick"></i></span></div>
    <div class="question"><span class="q">Have you had a joint replacement?</span><span class="answers">Yes<i class="tick"></i>No<i class="tick"></i></span></div>
    <div class="question"><span class="q">Women: Are you pregnant?</span><span class="answers">Yes<i class="tick"></i>No<i class="tick"></i>Possible<i class="tick"></i> or &nbsp;Breast Feeding? &nbsp;Yes<i class="tick"></i>No<i class="tick"></i></span></div>
  </section>

  <div class="turnover-tab">Please Turnover</div>
</main>
</body>
</html>
```